July 2022 Industrial Manufacturer Product Expo Mexico City

We manufacture large screws and fastners for large Mining equipment, Trains, large ships, airplanes, wind turbines, and so on. We also do custom work base on the customer needs. No matter the size we can make it.
We have a Expo coming up with companies all over the world. We have to stand out we are a family own business so our customer service will be above and beyond anyone can provide. We do not have a sales force to push our products and services we provide one on one service.
Plus@!! I'm looking for anything that you designers can come up with if it was your company to put on a business card, plus i want to do a 1 or 2 sided pamphlet, and then a website. We make Speciality Bolts for large mining equipment these bolts can be 3 to 4 foot long!!! Plus fasteners, Nuts, washers, any, size, strengths, special materials, we offer more of a ono on one customer service, We are a small company, family own, but can fulfill any type of orders. We can also provide special time lines for emergency orders. "We keep the machines running we here at KRV don't believe in down time" We want to hear any slogan based on our company to stand out.
Thanks i really appreciate all your work and options that we have to pick on. Plus just a thought we could possibly want to entertain a experience Marketing internet help maybe a employment possibility. Thanks

I need 2 cards one in Spanish and English Like the steel back ground maybe send me in some bright red and blue writing Same with the Black cards Please remove the word Military The logo KRV maybe integrate a picture of a Bolt 🔩 Thank you

Still looking for I need 2 cards one in Spanish and English Like the steel back ground maybe send me in some bright red and blue writing Same with the Black cards try bright writing Please remove the word Military The logo KRV maybe integrate a picture of a Bolt 🔩 Plus will need the company to make a brochure and website next Thank you

Target Market(s)

Large Mining, Ship, Train, Green Energy, VELM, and Government equipment. Throughout the World

Industry/Entity Type

We can Custom Manufacture any type of Fastners for Mining equipment, Trains, Ships, Green energy, Governments, or military projects. wind turbines,

Contact Information for Business Card

I attached the name and contact info that's on a card, plus the Company Logo. Would like industrial looking background with Bright Colors that will stand out!! If we can insert somewhere maybe on back that we "Custom Manufacture Any Size or Quantity Fastners for Large Mining Equipment, Trains, Ships, Green Energy Equipment or Government Projects

Font styles to use
Other font styles liked:
• You Pick, has to be bold, colorful standout, Professional looking Beable to read it.

Colors

Designer to choose colors to be used in the design.

Requirements
Must have
• Need in Spanish and English TO STANDOUT FROM THE REST OF THE EXPO!! See Business card details, Rounded corners
Nice to have
• Can i see some of the darker cards with Bright Red and Blue letters I like to see the different type of card material, heavy thickness, plastic, transparent, Metal types, Bright Colors, I saw like Raised letters like on the logo.

```html
<!DOCTYPE html>
<html lang="es">
<head>
<meta charset="utf-8">
<title>KRV – Tarjetas de presentación</title>
<link rel="stylesheet" href="https://fonts.googleapis.com/css2?family=Source+Sans+3:wght@600;700&display=swap">
<style>
  :root {
    --backdrop: #2a2a2a;
    --card: #b9b9b9;
    --navy: #0e1f86;
    --red: #ec1c24;
    --rule: #8a8a8a;
    --steel-light: #c9c9c9;
    --steel-dark: #8f8f8f;
  }
  * { margin: 0; padding: 0; box-sizing: border-box; }
  html, body {
    width: 1093px; height: 1200px; overflow: hidden;
    background: var(--backdrop);
    font-family: "Source Sans 3", sans-serif;
  }
  .canvas { position: relative; width: 1093px; height: 1200px; }
  .card {
    position: absolute;
    background: var(--card);
    overflow: hidden;
    text-align: center;
  }
  .card--front { left: 265px; top: 226px; width: 578px; height: 357px; }
  .card--back  { left: 265px; top: 621px; width: 581px; height: 357px; }

  .brand {
    position: absolute; left: 0; right: 0;
    font-weight: 700; font-size: 86px; line-height: 1;
    letter-spacing: 10px; color: var(--navy);
  }
  .card--front .brand { top: 58px; }
  .card--back .brand  { top: 72px; z-index: 2; }

  .holder {
    position: absolute; top: 186px; left: 0; right: 0;
    font-weight: 600; font-size: 20px; color: var(--navy);
  }
  .rule {
    position: absolute; left: 50%; width: 74px; height: 1px;
    margin-left: -37px; background: var(--rule);
  }
  .rule--top { top: 223px; }
  .rule--bottom { top: 284px; }
  .quotes {
    position: absolute; top: 228px; left: 0; right: 0;
    font-weight: 600; font-size: 18px; line-height: 23px; color: var(--red);
  }
  .phones {
    position: absolute; top: 293px; left: 0; right: 0;
    display: flex; justify-content: center; align-items: center; gap: 12px;
    font-weight: 600; font-size: 18px; color: var(--red);
  }
  .phone { display: flex; align-items: center; gap: 4px; }
  .phone svg { width: 15px; height: 15px; fill: var(--navy); }

  .bolt-photo {
    position: absolute; left: 50px; top: 0; width: 518px; height: 350px;
    background: linear-gradient(160deg, var(--steel-light) 0%, #a9a9a9 45%, var(--steel-dark) 100%);
    opacity: .55;
    border-radius: 40px 12px 30px 60px;
  }
  .services {
    position: absolute; top: 221px; left: 0; right: 0; z-index: 2;
    font-weight: 600; font-size: 18px; line-height: 23.5px; color: var(--red);
  }
</style>
</head>
<body>
<main class="canvas">

  <section class="card card--front" aria-label="Frente de la tarjeta">
    <div class="brand">KRV</div>
    <p class="holder">Lic.Mariela Santos Ortega</p>
    <span class="rule rule--top"></span>
    <p class="quotes">Cotizaciones en<br>tornilleriakrv.ventas@correo.mx</p>
    <span class="rule rule--bottom"></span>
    <div class="phones">
      <span class="phone">
        <svg viewBox="0 0 24 24" aria-hidden="true"><path d="M6.6 10.8a15.1 15.1 0 0 0 6.6 6.6l2.2-2.2a1 1 0 0 1 1-.25 11.4 11.4 0 0 0 3.6.57 1 1 0 0 1 1 1V20a1 1 0 0 1-1 1A17 17 0 0 1 3 4a1 1 0 0 1 1-1h3.5a1 1 0 0 1 1 1c0 1.25.2 2.45.57 3.57a1 1 0 0 1-.25 1z"/></svg>
        8710004152
      </span>
      <span class="phone">
        <svg viewBox="0 0 24 24" aria-hidden="true"><path d="M7 1h10a2 2 0 0 1 2 2v18a2 2 0 0 1-2 2H7a2 2 0 0 1-2-2V3a2 2 0 0 1 2-2zm0 3v14h10V4zm5 15.5a1 1 0 1 0 0 2 1 1 0 0 0 0-2z"/></svg>
        8710006283
      </span>
    </div>
  </section>

  <section class="card card--back" aria-label="Reverso de la tarjeta">
    <div class="bolt-photo" role="img" aria-label="Fotografía de un perno metálico grande en gris, difuminado como fondo"></div>
    <div class="brand">KRV</div>
    <p class="services">
      Fabricación personalizada Cualquier tamaño o<br>
      Sujetadores de Cantidad para Gran Minería<br>
      Equipos Trenes, Barcos, Energía Verde<br>
      Equipos o Proyectos Gubernamentales
    </p>
  </section>

</main>
</body>
</html>
```